Product Design for VelaMira

Design Brief for VelaMira Product Packaging

Objective:
Create a cohesive, elegant, and brand-consistent packaging design for the VelaMira product line. The signature visual theme should reflect luxury, femininity, and clean beauty values.

---

🎨 Core Design Direction

Unified Aesthetic: All containers must prominently feature the floral pattern shown in "Pattern Reference: Image 3". This design serves as the brand's signature aesthetic and must be applied uniformly across all SKUs.

Brand Logo Placement: The VelaMira logo (provided) should be clearly visible and harmoniously integrated into the patterned background.

Color Palette: Base colors should complement the brand’s primary palette: black, blush pink, and white.

---

🧴 Product-Specific Packaging Specifications

1. Mascara

Bottle Type: Sleek mascara tube with a wand applicator

Capacity: 5ml

Design: Use floral pattern from Pattern Reference Image 3. Ensure the pattern does not obstruct the readability of the logo or any regulatory text.

2. Eyebrow Growth Serum

Bottle Type: 5ml tube with fine-tip brush applicator

Capacity: 5ml

Design: Same floral pattern, scaled and applied proportionally to match the mascara for consistency

3. Eyelash Growth Serum

Bottle Type: 5ml tube with fine-tip brush (similar to the eyebrow serum, unless otherwise advised)

Capacity: 5ml

Design: Identical styling to maintain unity across lash & brow products

4. Anti-Aging Serum or Lotion

Bottle Type: 30ml airless pump bottle (preferred for hygiene and product stability)

Capacity: 30ml

Design: Apply floral pattern from Pattern Reference and scale appropriately for larger surface area

5. Hair Growth Spray

Bottle Type: 50ml fine mist spray bottle

Capacity: 50ml

Design: Pattern applied and scaled for taller profile; maintain visual harmony with skincare line

---

📦 Additional Notes

Please ensure packaging aligns with clean beauty standards (no overly glossy plastic finishes, avoid excessive secondary packaging unless sustainable).

Materials should be eco-conscious where possible.

If embossing, foil stamping, or UV finishing is available for logo accents, please suggest options.

```html
<!DOCTYPE html>
<html lang="en">
<head>
<meta charset="utf-8">
<title>VelaMira Eyelash Growth Serum – Label</title>
<link rel="stylesheet" href="https://fonts.googleapis.com/css2?family=Lato:wght@400;700&family=Libre+Bodoni:wght@400;500&display=swap">
<style>
  :root {
    --canvas: #e4e5e5;
    --blush-light: #fdf1ea;
    --blush-mid: #f8d6c3;
    --blush-deep: #f2bfa3;
    --panel: #fffcfa;
    --ink: #141414;
    --accent: #e9946c;
  }
  * { margin: 0; padding: 0; box-sizing: border-box; }
  html, body { width: 1200px; height: 1200px; overflow: hidden; background: var(--canvas); }
  body { position: relative; font-family: "Lato", sans-serif; color: var(--ink); }

  .label {
    position: absolute; left: 253px; top: 100px;
    width: 694px; height: 1000px; overflow: hidden;
  }
  .floral-pattern {
    position: absolute; inset: 0;
    background:
      radial-gradient(circle at 20% 15%, var(--blush-deep) 0, transparent 22%),
      radial-gradient(circle at 75% 40%, var(--blush-deep) 0, transparent 20%),
      radial-gradient(circle at 30% 70%, var(--blush-deep) 0, transparent 20%),
      radial-gradient(circle at 85% 88%, var(--blush-deep) 0, transparent 20%),
      linear-gradient(160deg, var(--blush-light), var(--blush-mid));
  }

  .panel { position: absolute; background: var(--panel); text-align: center; }
  .panel--front { left: 100px; top: 90px; width: 150px; height: 820px; }
  .panel--back  { left: 445px; top: 105px; width: 153px; height: 800px; }

  .brand-name {
    position: absolute; left: 55px; top: 278px;
    transform: translate(-50%, -50%) rotate(-90deg);
    font-family: "Libre Bodoni", serif; font-weight: 400;
    font-size: 88px; line-height: 1; white-space: nowrap; letter-spacing: -1px;
  }
  .product-name {
    position: absolute; left: 0; right: 0; top: 555px;
    font-weight: 700; font-size: 25px; line-height: 29px;
  }
  .product-claim {
    position: absolute; left: 0; right: 0; top: 658px;
    font-size: 19px; line-height: 26px;
  }
  .product-volume {
    position: absolute; left: 0; right: 0; top: 739px;
    font-size: 19px; line-height: 26px;
  }

  .info-block { font-size: 21px; line-height: 28px; padding: 22px 2px 0; }
  .info-block + .info-block { padding-top: 14px; }
  .info-block strong { font-weight: 700; display: block; }

  .claims { list-style: none; margin-top: 22px; }
  .claim { display: flex; flex-direction: column; align-items: center; height: 76px; }
  .claim svg { width: 50px; height: 50px; }
  .claim span { font-size: 9px; color: var(--accent); margin-top: 3px; font-weight: 700; }

  .distributor { font-size: 19px; line-height: 28px; margin-top: 8px; }
  .distributor b { font-weight: 700; }
</style>
</head>
<body>
  <section class="label">
    <div class="floral-pattern" role="img" aria-label="Blush peach floral pattern of blossoms and leaves"></div>

    <div class="panel panel--front">
      <div class="brand-name">VelaMira</div>
      <div class="product-name">Eyelash<br>Growth<br>Serum</div>
      <div class="product-claim">Longer +<br>Fuller Lashes</div>
      <div class="product-volume">5ml/<br>0.17 fl.oz.</div>
    </div>

    <div class="panel panel--back">
      <p class="info-block"><strong>Ingredients:</strong>Aqua,<br>Myristoyl<br>Pentapeptide<br>-17</p>
      <p class="info-block"><strong>Caution:</strong>Avoid direct<br>contact with<br>eyes. For<br>external use<br>only.</p>

      <ul class="claims">
        <li class="claim">
          <svg viewBox="0 0 50 50" fill="none" stroke="var(--accent)" stroke-width="2">
            <circle cx="25" cy="25" r="23"/>
            <path d="M21 13h8M22 13v9l-7 13h20l-7-13v-9"/>
            <path d="M12 12l26 26"/>
          </svg>
          <span>Paraben Free</span>
        </li>
        <li class="claim">
          <svg viewBox="0 0 50 50" fill="none" stroke="var(--accent)" stroke-width="2">
            <circle cx="25" cy="25" r="23"/>
            <path d="M15 26l7 7 13-15"/>
          </svg>
          <span>Dermatologist Tested</span>
        </li>
        <li class="claim">
          <svg viewBox="0 0 50 50" fill="none" stroke="var(--accent)" stroke-width="2">
            <circle cx="25" cy="25" r="23"/>
            <path d="M25 11c6 8 9 13 9 18a9 9 0 0 1-18 0c0-5 3-10 9-18z"/>
            <path d="M25 22v16M25 30l-4-4M25 34l4-4"/>
          </svg>
          <span>Strengthens Roots</span>
        </li>
        <li class="claim">
          <svg viewBox="0 0 50 50" fill="none" stroke="var(--accent)" stroke-width="2">
            <circle cx="25" cy="25" r="23"/>
            <path d="M25 11c6 8 9 13 9 18a9 9 0 0 1-18 0c0-5 3-10 9-18z"/>
          </svg>
          <span>Cruelty Free</span>
        </li>
      </ul>

      <p class="distributor">Distributed by<br><b>VelaMira</b>,<br>London, UK</p>
    </div>
  </section>
</body>
</html>
```